Book Cover Project

This is a printed journal front and back cover design. We like the current design, but it feels a little too flat / too simple.

NOTE: we are not looking for a total makeover, just a finishing / polishing of this cover.

Here is our other book cover: https://www.shelvora-books.example/Quiet-Studio-Ledger-Fine-Morning/dp/7093268415/ref=tmm_hrd_swatch_0?_encoding=UTF8&qid=&sr=
it's purple and yellow (mostly purple)
this one is yellow and we're thinking to add a purple bar at the bottom

Specs: 6 in x 9 in full bleed for print

```html
<!DOCTYPE html>
<html lang="en">
<head>
<meta charset="utf-8">
<title>Kindled Distance Journal — Cover</title>
<link rel="stylesheet" href="https://fonts.googleapis.com/css2?family=Arimo:wght@400;700&display=swap">
<style>
  :root {
    --cover-yellow: #FFD800;
    --ink: #000000;
    --author-tint: #F9E57A;
    --band-purple: #5053A4;
    --runner-tone: #E8C400;
  }
  html, body {
    margin: 0;
    padding: 0;
    width: 800px;
    height: 1200px;
    overflow: hidden;
  }
  .cover {
    position: relative;
    width: 800px;
    height: 1200px;
    background: var(--cover-yellow);
    font-family: "Arimo", Arial, sans-serif;
    color: var(--ink);
    overflow: hidden;
  }
  .title {
    margin: 0;
    font-size: inherit;
  }
  .title-line {
    position: absolute;
    margin: 0;
    line-height: 1;
    white-space: nowrap;
  }
  .title-top {
    font-weight: 400;
    font-size: 115px;
    top: 353px;
  }
  .title-top--lead { right: 582px; }
  .title-top--rest { left: 288px; }
  .runner-figure {
    position: absolute;
    left: 226px;
    top: 316px;
    width: 56px;
    height: 155px;
    border-radius: 28px 28px 6px 6px;
    background: linear-gradient(180deg, var(--runner-tone), var(--cover-yellow));
  }
  .title-middle {
    left: 0;
    width: 800px;
    text-align: center;
    top: 461px;
    font-weight: 700;
    font-size: 128px;
    letter-spacing: -5px;
    text-indent: -5px;
  }
  .title-bottom {
    left: 0;
    width: 798px;
    text-align: center;
    top: 576px;
    font-weight: 400;
    font-size: 117px;
  }
  .tagline {
    position: absolute;
    left: 0;
    width: 800px;
    top: 717px;
    margin: 0;
    text-align: center;
    font-weight: 700;
    font-size: 28px;
    line-height: 1;
  }
  .author-plate {
    position: absolute;
    left: 225px;
    top: 1066px;
    width: 349px;
    height: 55px;
    background: var(--author-tint);
    display: flex;
    align-items: center;
    justify-content: center;
  }
  .author-name {
    margin: 0;
    font-weight: 400;
    font-size: 24px;
    letter-spacing: 2px;
    text-transform: uppercase;
    line-height: 1;
  }
  .bottom-band {
    position: absolute;
    left: 0;
    bottom: 0;
    width: 800px;
    height: 37px;
    background: var(--band-purple);
  }
</style>
</head>
<body>
  <main class="cover">
    <h1 class="title" aria-label="Kindled Distance Journal">
      <span class="title-line title-top title-top--lead" aria-hidden="true">K</span>
      <span class="runner-figure" role="img" aria-label="Single-line drawing of a runner standing in for the letter I"></span>
      <span class="title-line title-top title-top--rest" aria-hidden="true">NDLED</span>
      <span class="title-line title-middle" aria-hidden="true">DISTANCE</span>
      <span class="title-line title-bottom" aria-hidden="true">JOURNAL</span>
    </h1>
    <p class="tagline">Run - Write - Transform</p>
    <div class="author-plate">
      <p class="author-name">Tobias Wrenfield</p>
    </div>
    <div class="bottom-band"></div>
  </main>
</body>
</html>
```